Business Card Design and Logo Needed

I need Business Cards and a Logo for my website and public speaking business which can be found at: www.corvina-lett.example

I'm looking for creative and unique ideas. Some business cards I've found online that I like can be found at:
http://gigbarrow.example/general/18-smokin-hot-business-card-designs/

and at

http://www.plumquarry.example/2009/04/50-creative-business-cards-of-50-graphic-designers/

```html
<!DOCTYPE html>
<html lang="en">
<head>
<meta charset="utf-8">
<title>Corvina Lett — Business Card</title>
<link rel="stylesheet" href="https://fonts.googleapis.com/css2?family=Questrial&family=Parisienne&display=swap">
<style>
  :root {
    --card-bg: #ffffff;
    --speaker-green: #66f23a;
    --philanthropist-blue: #0a78ff;
    --author-purple: #9a0cf5;
    --name-ink: #111111;
  }
  html, body {
    margin: 0;
    padding: 0;
    width: 780px;
    height: 1200px;
    overflow: hidden;
    background: var(--card-bg);
  }
  .card {
    position: relative;
    width: 780px;
    height: 1200px;
    background: var(--card-bg);
  }
  .roles {
    position: absolute;
    top: 218px;
    left: 0;
    width: 100%;
    margin: 0;
    padding: 0;
    list-style: none;
    text-align: center;
    font-family: "Questrial", "Century Gothic", sans-serif;
    font-size: 84px;
    line-height: 110px;
  }
  .role--speaker { color: var(--speaker-green); }
  .role--philanthropist { color: var(--philanthropist-blue); }
  .role--author { color: var(--author-purple); }
  .name {
    position: absolute;
    top: 790px;
    left: 0;
    width: 100%;
    margin: 0;
    text-align: center;
    font-family: "Parisienne", cursive;
    font-weight: 400;
    font-size: 132px;
    line-height: 170px;
    color: var(--name-ink);
  }
</style>
</head>
<body>
  <main class="card">
    <ul class="roles">
      <li class="role role--speaker">Speaker</li>
      <li class="role role--philanthropist">Philanthropist</li>
      <li class="role role--author">Author</li>
    </ul>
    <h1 class="name">Corvina Lett</h1>
  </main>
</body>
</html>
```